Boutique custom software development company needs new business card

Our nearly 20 year old custom software development company would like to better include the fact that we are now providing Bitcoin services. These new services are B2B include education (how to acquire and securely hold Bitcoin) and integrating Bitcoin payments into existing ecommerce sites or other existing systems. Please keep the card clean and simple. Attached is our current design and some other files. vextorial.com

Target Market(s)

businesses owners interested in long term relationship

Industry/Entity Type

Custom software development and Bitcoin

Contact Information for Business Card

Dale Parker, dale@vextorial.com, vextorial.com, (888) 555-VXTRL

Font styles to use
Other font styles liked:
• monospace

Requirements
Must have
• double-sided
Nice to have
• clean and simple
Should not have
• physical address

```html
<!DOCTYPE html>
<html lang="en">
<head>
<meta charset="utf-8">
<title>Vextorial Business Card</title>
<link rel="stylesheet" href="https://fonts.googleapis.com/css2?family=Montserrat:wght@400;500;700;800&family=Lato:wght@400;700&display=swap">
<style>
  :root {
    --backdrop: #7b7b7b;
    --card-white: #ffffff;
    --brand-blue: #3b71b7;
    --brand-orange: #f07a22;
    --edge-orange: #e08a45;
    --text-grey: #5a5a5a;
  }
  * { box-sizing: border-box; margin: 0; padding: 0; }
  html, body { width: 1200px; height: 801px; overflow: hidden; }
  body {
    background: var(--backdrop);
    display: flex;
    align-items: center;
    justify-content: center;
    gap: 48px;
    font-family: "Montserrat", sans-serif;
  }
  .card {
    width: 525px;
    height: 300px;
    position: relative;
    border-bottom: 4px solid var(--edge-orange);
    box-shadow: 0 12px 28px rgba(0,0,0,0.28);
  }
  .card--front { background: var(--card-white); }
  .card--back { background: var(--brand-blue); }

  /* front */
  .front-brand {
    position: absolute;
    left: 42px;
    top: 0;
    bottom: 0;
    display: flex;
    align-items: center;
    gap: 12px;
  }
  .front-brand__square {
    width: 22px;
    height: 22px;
    background: var(--brand-orange);
  }
  .front-brand__name {
    font-weight: 800;
    font-size: 30px;
    letter-spacing: 1px;
    color: var(--brand-blue);
  }
  .contact {
    position: absolute;
    left: 300px;
    top: 0;
    bottom: 0;
    display: flex;
    flex-direction: column;
    justify-content: center;
    color: var(--text-grey);
    font-size: 13px;
    line-height: 1.55;
  }
  .contact__name {
    font-weight: 700;
    font-size: 20px;
    letter-spacing: 0.5px;
    line-height: 1.1;
  }
  .contact__first { color: var(--brand-orange); }
  .contact__last { color: var(--brand-blue); }
  .contact__title {
    font-size: 13px;
    letter-spacing: 1px;
    margin-bottom: 10px;
  }
  .contact__line { display: flex; align-items: center; gap: 6px; }
  .contact__icon { width: 10px; height: 10px; flex: none; }
  .web-accent { color: var(--brand-blue); }

  /* back */
  .back-lockup {
    position: absolute;
    inset: 0;
    display: flex;
    flex-direction: column;
    align-items: center;
    justify-content: center;
    gap: 6px;
  }
  .back-lockup__name {
    font-weight: 800;
    font-size: 56px;
    letter-spacing: 2px;
    color: var(--card-white);
    line-height: 1;
  }
  .back-lockup__tagline {
    font-family: "Lato", sans-serif;
    font-size: 22px;
    color: var(--card-white);
  }
  .back-lockup__services {
    margin-top: 10px;
    font-family: "Lato", sans-serif;
    font-weight: 700;
    font-size: 14px;
    letter-spacing: 1.5px;
    text-transform: uppercase;
    color: var(--card-white);
    display: flex;
    align-items: center;
    gap: 10px;
  }
  .services__dot {
    width: 6px;
    height: 6px;
    background: var(--brand-orange);
    border-radius: 50%;
  }
</style>
</head>
<body>
  <section class="card card--front" aria-label="Card front">
    <div class="front-brand">
      <span class="front-brand__square"></span>
      <span class="front-brand__name">VEXTORIAL</span>
    </div>
    <div class="contact">
      <p class="contact__name"><span class="contact__first">DALE</span> <span class="contact__last">PARKER</span></p>
      <p class="contact__title">DIRECTOR</p>
      <p class="contact__line">
        <svg class="contact__icon" viewBox="0 0 10 10"><path d="M2 1 L4 1 L4.6 3 L3.4 3.8 Q4.4 5.8 6.2 6.6 L7 5.4 L9 6 L9 8 Q5 9 1 3 Z" fill="#3b71b7"/></svg>
        <span>(888) 555-VXTRL</span>
      </p>
      <p class="contact__line">
        <svg class="contact__icon" viewBox="0 0 10 10"><rect x="0.6" y="2" width="8.8" height="6" fill="none" stroke="#3b71b7" stroke-width="1"/><path d="M0.6 2 L5 5.4 L9.4 2" fill="none" stroke="#3b71b7" stroke-width="1"/></svg>
        <span>dale@vextorial.com</span>
      </p>
      <p class="contact__line">
        <svg class="contact__icon" viewBox="0 0 10 10"><circle cx="5" cy="5" r="4.2" fill="none" stroke="#3b71b7" stroke-width="1"/><ellipse cx="5" cy="5" rx="1.8" ry="4.2" fill="none" stroke="#3b71b7" stroke-width="0.8"/><line x1="0.8" y1="5" x2="9.2" y2="5" stroke="#3b71b7" stroke-width="0.8"/></svg>
        <span>www.<span class="web-accent">vextorial</span>.com</span>
      </p>
    </div>
  </section>

  <section class="card card--back" aria-label="Card back">
    <div class="back-lockup">
      <p class="back-lockup__name">VEXTORIAL</p>
      <p class="back-lockup__tagline">developer of custom applications</p>
      <p class="back-lockup__services">
        <span>Custom Software</span>
        <span class="services__dot"></span>
        <span>Bitcoin Services</span>
      </p>
    </div>
  </section>
</body>
</html>
```